Sonic Vale

Rebrand current website and move it to SonicVale.com. Looking for a professional, eye catching, top 10 in World type website. My current website is: https://madebytorven.sitepadhub.com/sonicvale
I would like it moved to sonicvale.com.

```html
<!DOCTYPE html>
<html lang="en">
<head>
<meta charset="utf-8">
<title>Sonic Vale — Torven Mercer</title>
<link rel="stylesheet" href="https://fonts.googleapis.com/css2?family=Electrolize&family=Jura:wght@400;500;600&display=swap">
<style>
:root{
  --ink:#111111;
  --black:#000000;
  --white:#ffffff;
  --blue:#0b4ee0;
  --blue-soft:#a9c3ec;
  --shop-bg:#f0f0f0;
  --video-bg:#1c1b1a;
  --footer-bg:#0d0d0d;
  --text:#222222;
}
*{margin:0;padding:0;box-sizing:border-box}
html,body{width:1200px;height:3046px;overflow:hidden;background:var(--white)}
body{position:relative;font-family:"Jura",sans-serif;color:var(--text)}
.abs{position:absolute}

/* header */
.site-header{left:0;top:0;width:1200px;height:97px;background:var(--black)}
.brand{left:142px;top:34px;font-family:"Electrolize",sans-serif;font-size:27px;color:var(--white);letter-spacing:1px}
.nav-item{position:absolute;top:44px;font-family:"Electrolize",sans-serif;font-size:11px;color:var(--white);letter-spacing:.6px;white-space:nowrap}
.nav-item.active{color:var(--blue)}
.nav-item.active::after{content:"";position:absolute;left:0;right:0;top:17px;height:1px;background:var(--blue)}

/* hero */
.hero{left:0;top:97px;width:1200px;height:573px}
.hero-title{left:0;width:1200px;top:245px;text-align:center;font-family:"Electrolize",sans-serif;font-size:49px;color:var(--white);letter-spacing:2px}
.hero-sub{left:0;width:1200px;top:306px;text-align:center;font-size:15px;color:var(--white);letter-spacing:9px;font-weight:500}
.btn-outline{left:515px;top:354px;width:170px;height:50px;border:2px solid var(--white);border-radius:26px;color:var(--white);font-family:"Electrolize",sans-serif;font-size:16px;display:flex;align-items:center;justify-content:center;letter-spacing:.5px}
.dot{top:612px;width:8px;height:8px;border-radius:50%;background:var(--white)}
.dot.off{background:transparent;border:1px solid var(--white)}

/* intro */
.intro-title{left:144px;top:735px;font-family:"Electrolize",sans-serif;font-weight:400;font-size:40px;color:var(--ink);letter-spacing:1.5px}
.intro-copy{left:144px;top:794px;width:452px;font-size:12.4px;line-height:21.6px;color:var(--ink);font-weight:500}
.btn-blue{background:var(--blue);color:var(--white);border-radius:28px;font-family:"Electrolize",sans-serif;display:flex;align-items:center;justify-content:center;letter-spacing:.5px}
.intro-btn{left:144px;top:958px;width:170px;height:53px;font-size:16px;border:2px solid #2d63d6}
.intro-photo{left:625px;top:730px;width:433px;height:309px;border:2px solid #5d8fe0;background:linear-gradient(180deg,#1a1a22 0%,#3a2e3a 30%,#22201c 55%,#4a4538 80%,#1d1c18 100%)}

/* video */
.video{left:0;top:1128px;width:1200px;height:449px;background:radial-gradient(ellipse at 30% 60%,#3a3128 0%,#252220 45%,var(--video-bg) 100%)}
.video-title{left:0;width:1200px;top:1222px;text-align:center;font-family:"Electrolize",sans-serif;font-weight:400;font-size:36px;color:var(--white);letter-spacing:1px}
.video-sub{left:0;width:1200px;top:1281px;text-align:center;font-size:12px;color:var(--white);font-weight:500}

/* shop */
.shop{left:0;top:1577px;width:1200px;height:575px;background:var(--shop-bg)}
.section-title{left:0;width:1200px;text-align:center;font-family:"Electrolize",sans-serif;font-weight:400;font-size:38px;color:var(--ink);letter-spacing:2px}
.product-photo{top:1708px;width:446px;height:280px}
.product-name{top:2012px;width:446px;text-align:center;font-family:"Electrolize",sans-serif;font-size:21px;color:#333;letter-spacing:1.5px}
.product-price{top:2055px;width:446px;text-align:center;font-size:17px;color:#444;font-weight:500}

/* about */
.about-sub{left:144px;top:2310px;font-family:"Electrolize",sans-serif;font-weight:400;font-size:28px;color:var(--ink);letter-spacing:1px}
.about-copy{left:144px;top:2365px;width:352px;font-size:14px;line-height:28px;color:#333;font-weight:500}
.about-btn{left:144px;top:2610px;width:162px;height:48px;font-size:17px}
.about-photo-frame{left:537px;top:2293px;width:519px;height:393px;border:5px solid var(--blue-soft)}
.about-photo{left:542px;top:2298px;width:509px;height:383px;background:linear-gradient(160deg,#3a3038 0%,#5a4a52 35%,#2a2228 65%,#c9c4c2 100%)}

/* footer */
.footer-band{left:0;top:2767px;width:1200px;height:279px;background:var(--footer-bg)}
.footer-heading{position:absolute;top:2812px;font-family:"Electrolize",sans-serif;font-weight:400;font-size:14px;color:var(--white);letter-spacing:.5px;white-space:nowrap}
.footer-link{font-size:12px;color:var(--white);font-weight:500}
.contact-line{left:519px;font-size:12px;color:var(--white);font-weight:500;display:flex;align-items:center;gap:4px}
.email-field{left:801px;top:2845px;width:255px;height:33px;background:var(--white);font-size:11px;color:#333;padding-left:17px;display:flex;align-items:center;font-weight:600}
.submit-btn{left:922px;top:2893px;width:135px;height:40px;font-size:14px;border-radius:22px}
.footer-rule{left:144px;top:2990px;width:912px;height:1px;background:#2b2b2b}
.copyright{left:144px;top:3010px;font-size:10px;color:var(--white);font-weight:500}
.social{top:3007px;width:14px;height:14px;border-radius:50%;background:var(--white)}
</style>
</head>
<body>

<header class="abs site-header">
  <div class="abs brand">SONIC VALE</div>
  <nav>
    <span class="nav-item active" style="left:524px">HOME</span>
    <span class="nav-item" style="left:605px">SHOP</span>
    <span class="nav-item" style="left:683px">BOOK ONLINE</span>
    <span class="nav-item" style="left:808px">BLOG</span>
    <span class="nav-item" style="left:887px">CONTACT US</span>
    <span class="nav-item" style="left:1008px">CART (0)</span>
  </nav>
</header>

<svg class="abs hero" viewBox="0 0 1200 573" role="img" aria-label="Producer wearing headphones in a dark home studio">
  <defs>
    <radialGradient id="heroGlow" cx="0.5" cy="0.35" r="0.7">
      <stop offset="0" stop-color="#3c3c3c"/>
      <stop offset="0.6" stop-color="#1e1e1e"/>
      <stop offset="1" stop-color="#0b0b0b"/>
    </radialGradient>
  </defs>
  <polygon points="0,0 1200,0 1200,531 0,573" fill="url(#heroGlow)"/>
</svg>
<div class="abs hero-title">JOURNEY WITH TORVEN MERCER</div>
<div class="abs hero-sub">Music Producer Portfolio</div>
<div class="abs btn-outline">LEARN MORE</div>
<span class="abs dot off" style="left:580px"></span>
<span class="abs dot" style="left:596px"></span>
<span class="abs dot" style="left:612px"></span>

<section>
  <h1 class="abs intro-title">TORVEN MERCER</h1>
  <p class="abs intro-copy">Intricate but gritty music producer who specializes in all phases of music production.A a Certified Audio Engineer and a beat maker of genres(hip hop,trap,edm,R&amp;B etc..)I think it's most important to take pride in quality sound when your involved in any step of the process of creating! Your Music will be professional mixed and mastered to a industry standard.</p>
  <div class="abs btn-blue intro-btn">READ MORE</div>
  <div class="abs intro-photo" role="img" aria-label="Mixing console in front of a live stage show"></div>
</section>

<section>
  <div class="abs video" role="img" aria-label="Hands playing a piano keyboard in low light"></div>
  <h2 class="abs video-title">OUR VIDEO</h2>
  <div class="abs video-sub">Torven nd OFF THE LINE (Remastered)</div>
  <svg class="abs" style="left:563px;top:1338px" width="74" height="74" viewBox="0 0 74 74">
    <circle cx="37" cy="37" r="35" fill="#111" stroke="#fff" stroke-width="2"/>
    <polygon points="28,21 28,53 55,37" fill="#fff"/>
  </svg>
</section>

<section>
  <div class="abs shop"></div>
  <h2 class="abs section-title" style="top:1627px">OUR SHOP</h2>
  <div class="abs product-photo" style="left:144px;background:linear-gradient(160deg,#9aa3b8 0%,#4a5a80 40%,#2c3552 100%)" role="img" aria-label="Close view of a blue mixing desk"></div>
  <div class="abs product-photo" style="left:610px;background:linear-gradient(180deg,#1c1e22 0%,#4a4e55 45%,#8f979c 100%)" role="img" aria-label="Faders on a mixing console"></div>
  <div class="abs product-name" style="left:144px">MIXING AND MASTERING</div>
  <div class="abs product-name" style="left:610px">BOOK A SESSION</div>
  <div class="abs product-price" style="left:144px">$150.00</div>
  <div class="abs product-price" style="left:610px">$120.00</div>
</section>

<section>
  <h2 class="abs section-title" style="top:2206px">ABOUT US</h2>
  <h3 class="abs about-sub">A Life Steeped in Sound</h3>
  <p class="abs about-copy">Hailing from Bayou Crest, Torven has always pushed himself to achieve more success in his music career. Looking to perfect his technical abilities and develop his own unique style, Torven draws upon his Bayou Crest roots and lifelong passion for music. Get in touch to learn more about his background, experience, and latest projects.</p>
  <div class="abs btn-blue about-btn">GET IN TOUCH</div>
  <div class="abs about-photo-frame"></div>
  <div class="abs about-photo" role="img" aria-label="Portrait of the producer in his studio"></div>
</section>

<footer>
  <div class="abs footer-band"></div>
  <h4 class="footer-heading" style="left:144px">Navigation</h4>
  <div class="abs footer-link" style="left:144px;top:2845px">Home</div>
  <div class="abs footer-link" style="left:144px;top:2869px">Shop</div>
  <div class="abs footer-link" style="left:144px;top:2893px">Book Online</div>
  <div class="abs footer-link" style="left:144px;top:2917px">Blog</div>
  <div class="abs footer-link" style="left:144px;top:2941px">Contact Us</div>
  <div class="abs footer-link" style="left:336px;top:2845px">Testimonials</div>
  <div class="abs footer-link" style="left:336px;top:2869px">FAQ's</div>
  <div class="abs footer-link" style="left:336px;top:2893px">Site Map</div>

  <h4 class="footer-heading" style="left:519px">Contact Info</h4>
  <div class="abs contact-line" style="top:2849px">
    <svg width="9" height="12" viewBox="0 0 9 12"><path d="M4.5 0C2 0 0 2 0 4.5 0 8 4.5 12 4.5 12S9 8 9 4.5C9 2 7 0 4.5 0zm0 6.3a1.8 1.8 0 110-3.6 1.8 1.8 0 010 3.6z" fill="#fff"/></svg>Bayou Crest,Louisiana</div>
  <div class="abs contact-line" style="top:2884px">
    <svg width="12" height="10" viewBox="0 0 12 10"><rect x=".6" y=".6" width="10.8" height="8.8" fill="none" stroke="#fff" stroke-width="1.2"/><path d="M.6 .8L6 5.5 11.4.8" fill="none" stroke="#fff" stroke-width="1.2"/></svg>producedbytorven@mailbox.com</div>
  <div class="abs contact-line" style="top:2920px">
    <svg width="10" height="10" viewBox="0 0 10 10"><path d="M2 0l2 2.5-1.2 1.3a6 6 0 003.4 3.4L7.5 6 10 8 8.5 10C4 10 0 6 0 1.5z" fill="#fff"/></svg>555-013-2480</div>

  <h4 class="footer-heading" style="left:799px">Join Our Newsletter</h4>
  <div class="abs email-field">Email Address</div>
  <div class="abs btn-blue submit-btn">SUBMIT NOW</div>

  <div class="abs footer-rule"></div>
  <div class="abs copyright">Copyrights © 2021 Sonic Vale. All rights reserved.</div>
  <span class="abs social" style="left:983px"></span>
  <span class="abs social" style="left:1008px"></span>
  <span class="abs social" style="left:1040px"></span>
</footer>

</body>
</html>
```